Business Card Design Project

I need a business card design for an Organic drive thru coffee kiosk. We will serve organic coffee, teas & smoothies and will serve healthy breakfast food/snacks for people on the go.
I want the card to have 2-3 colors max (earthy colors like browns, greens and so on).
I have attached the logo I want used and would love to play off the theme of "balance."
Include:
Sun-Leaf Coffee
address: 3712 Pelwin Ct. Raleigh, NC 27699
phone: 919-555-0143
website: www.sun-leaf.com (website is not up yet but still include it on card)
email: Dorothy@sun-leaf.com
I want one of the following sayings somewhere on the card (the front or back is fine):
"Eat & Drink Well, on the run!"
"Break the fast with Sun-Leaf"
Maybe on the back list what we offer:
-Organic coffee, espresso & tea
-Blendora smoothies & protein shakes
-Zippy Tonic (100% fresh local fruit and veggies)
-Vital Nibbles
College age to 55
Business

```html
<!DOCTYPE html>
<html lang="en">
<head>
<meta charset="utf-8">
<title>Sun-Leaf Coffee – Business Card</title>
<link href="https://fonts.googleapis.com/css2?family=Dancing+Script:wght@600&family=Open+Sans:wght@400;600&display=swap" rel="stylesheet">
<style>
  :root {
    --backdrop: #eab6a5;
    --card-white: #fbfaf8;
    --brown: #7b3a27;
    --brown-soft: #b5867a;
    --cream: #f3e2d8;
    --ink: #3a2a24;
    --faint: rgba(120, 90, 80, 0.07);
  }
  * { box-sizing: border-box; margin: 0; padding: 0; }
  html, body {
    width: 1200px; height: 1000px; overflow: hidden;
    background: var(--backdrop);
    font-family: "Open Sans", Arial, sans-serif;
  }
  .card {
    position: absolute; left: 250px;
    width: 700px; height: 400px;
    overflow: hidden;
    box-shadow: 0 14px 30px rgba(90, 40, 30, 0.25);
  }
  /* Front */
  .card-front { top: 60px; background: var(--card-white); }
  .front-deco {
    position: absolute; left: 300px; top: 20px;
    width: 300px; height: 300px; border-radius: 50%;
    background: var(--faint);
  }
  .brand {
    position: absolute; left: 40px; top: 120px; width: 280px;
    text-align: center;
  }
  .brand-dot {
    width: 72px; height: 72px; border-radius: 50%;
    background: var(--brown); margin: 0 auto 14px;
  }
  .brand-name {
    font-family: "Open Sans", Arial, sans-serif;
    font-weight: 600; font-size: 44px; color: var(--brown);
    letter-spacing: -0.5px; line-height: 1;
  }
  .divider {
    position: absolute; left: 345px; top: 80px;
    width: 1px; height: 220px; background: var(--brown);
  }
  .company-title {
    position: absolute; left: 380px; top: 80px;
    font-family: "Dancing Script", cursive;
    font-weight: 600; font-size: 38px; color: var(--brown);
  }
  .contact-list {
    position: absolute; left: 384px; top: 150px;
    list-style: none; font-size: 16px; color: var(--ink); line-height: 1.35;
  }
  .contact-list li { display: flex; align-items: flex-start; gap: 8px; }
  .contact-list li + li { margin-top: 2px; }
  .contact-list svg { flex: none; width: 15px; height: 15px; margin-top: 3px; fill: var(--ink); }
  .contact-list .no-icon { padding-left: 23px; }
  .tagline-band {
    position: absolute; left: 0; bottom: 0; width: 100%; height: 48px;
    background: var(--brown); color: var(--cream);
    font-size: 17px; display: flex; align-items: center; justify-content: center;
  }
  /* Back */
  .card-back { top: 540px; background: var(--brown); }
  .back-band {
    position: absolute; left: 0; top: 18px; width: 100%; height: 70px;
    background: var(--brown-soft);
    display: flex; align-items: center; justify-content: center; gap: 10px;
  }
  .back-band .brand-dot { width: 26px; height: 26px; margin: 0; }
  .back-band .brand-name { font-size: 24px; }
  .back-watermark {
    position: absolute; left: 260px; top: 285px;
    font-weight: 600; font-size: 82px; color: rgba(0,0,0,0.1);
    letter-spacing: -1px;
  }
  .offer-list {
    position: absolute; left: 110px; top: 120px;
    list-style: none;
    font-family: "Dancing Script", cursive; font-weight: 600;
    font-size: 25px; color: var(--cream); line-height: 1.35;
  }
  .offer-list li:nth-child(2) { padding-left: 14px; }
  .offer-list li:nth-child(3) { padding-left: 28px; }
  .offer-list li:nth-child(4) { padding-left: 42px; }
</style>
</head>
<body>
  <section class="card card-front">
    <div class="front-deco"></div>
    <div class="brand">
      <div class="brand-dot"></div>
      <div class="brand-name">Sun-Leaf</div>
    </div>
    <div class="divider"></div>
    <h1 class="company-title">Sun-Leaf Coffee</h1>
    <ul class="contact-list">
      <li>
        <svg viewBox="0 0 24 24" aria-hidden="true"><path d="M12 2a7 7 0 0 0-7 7c0 5.2 7 13 7 13s7-7.8 7-13a7 7 0 0 0-7-7zm0 9.5A2.5 2.5 0 1 1 12 6.5a2.5 2.5 0 0 1 0 5z"/></svg>
        <span>3712 Pelwin Ct. Raleigh, NC<br>27699</span>
      </li>
      <li>
        <svg viewBox="0 0 24 24" aria-hidden="true"><path d="M6.6 10.8a15.1 15.1 0 0 0 6.6 6.6l2.2-2.2a1 1 0 0 1 1-.25 11.4 11.4 0 0 0 3.6.57 1 1 0 0 1 1 1V20a1 1 0 0 1-1 1A17 17 0 0 1 3 4a1 1 0 0 1 1-1h3.5a1 1 0 0 1 1 1c0 1.25.2 2.45.57 3.57a1 1 0 0 1-.25 1z"/></svg>
        <span>919-555-0143</span>
      </li>
      <li>
        <svg viewBox="0 0 24 24" aria-hidden="true"><path d="M3 5h18v14H3zm2 2v.5l7 4.5 7-4.5V7zm0 3v7h14v-7l-7 4.5z"/></svg>
        <span>Dorothy@sun-leaf.com</span>
      </li>
      <li class="no-icon">www.sun-leaf.com</li>
    </ul>
    <div class="tagline-band">Break the fast with Sun-Leaf</div>
  </section>

  <section class="card card-back">
    <div class="back-band">
      <div class="brand-dot"></div>
      <div class="brand-name">Sun-Leaf</div>
    </div>
    <div class="back-watermark" aria-hidden="true">Sun-Leaf</div>
    <ul class="offer-list">
      <li>-Organic coffee, espresso &amp; tea</li>
      <li>-Blendora smoothies &amp; protein shakes</li>
      <li>-Zippy Tonic (100% fresh local fruit and veggies)</li>
      <li>-Vital Nibbles</li>
    </ul>
  </section>
</body>
</html>
```